Brand and Marketing Coach Needs PDF Designed

I have content that i need placed into a simple but great PDF design. The PDF is about the formula I use to build personal brands. This is geared towards entrepreneurs, experts, coaches, therapists, wellness practitioners, and indpendent business owners who serve to improve the lives of others.
The company name is changing from TorvelCast to Selling with the Village (I don't have that logo yet, so working backwards a bit. For now, the TorvelCast logo can be used.) My brand is NOT formal and corporate, but it's also not neon-pink and screaming at you. It's down to earth, hip, a bit modern but warm. It's about no BS and authenticity. The final deliverable should make the reader feel focused, smart, motivated and hopeful.

Target Market(s)

Conscious entrepreneurs and small business owners. this one is specifically for pharmacy entrepreneurs but this will be used for various audiences later.

Font styles to use
Sans Serif

Colors
eaf1f7
3377b5
6b449b
f37122
faa54b
f68e4e
ffc214

Requirements
Must have
• Modern design. colors that match logo - 4e5583 (i think that is the blue.) d65a40.
• Could have these colors as well: c6a254, 01bcc3
• But open to other colors
Nice to have
• I'd like to see some ways to make this PDF simple and readable, and eye-catching. I'd also like to use the uploaded ebooks for design ideas.
Should not have
• neon colors, clip art

```html
<!DOCTYPE html>
<html lang="en">
<head>
<meta charset="utf-8">
<title>The Personal Brand Compass – Cover Page Revised</title>
<link rel="stylesheet" href="https://fonts.googleapis.com/css2?family=Oswald:wght@400;500&family=Lato:ital,wght@0,400;0,700;1,400&family=La+Belle+Aurore&display=swap">
<style>
  :root {
    --stage: #000000;
    --stage-text: #ffffff;
    --navy: #4e5583;
    --gold: #d6ae5f;
    --mist: #b3c4d3;
    --ink: #222222;
    --paper: #ffffff;
    --photo-dark: #6f6f6f;
    --photo-mid: #b9b9b9;
    --photo-light: #eeeeee;
    --accent: #d65a40;
  }
  * { box-sizing: border-box; margin: 0; padding: 0; }
  html, body {
    width: 1200px; height: 1000px; overflow: hidden;
    background: var(--stage);
  }
  .stage { position: relative; width: 1200px; height: 1000px; }
  .stage-label {
    position: absolute; top: 88px; left: 0; width: 100%;
    text-align: center; color: var(--stage-text);
    font-family: "Lato", sans-serif; font-weight: 400; font-size: 34px; letter-spacing: 1.5px;
  }
  .cover {
    position: absolute; left: 146px; top: 232px;
    width: 886px; height: 683px; background: var(--paper); overflow: hidden;
  }
  .title-band {
    position: absolute; left: 0; top: 0; width: 100%; height: 292px;
    background: var(--navy);
  }
  .title-frame {
    position: absolute; left: 118px; top: 33px; width: 663px; height: 230px;
    border: 5px solid var(--gold);
    color: var(--gold); font-family: "Oswald", sans-serif; text-align: center;
  }
  .title-main {
    position: absolute; top: 18px; left: 0; width: 100%;
    font-size: 101px; line-height: 1; font-weight: 400; letter-spacing: 0.5px;
    white-space: nowrap;
  }
  .title-sub {
    position: absolute; top: 128px; left: 0; width: 100%;
    font-size: 70px; line-height: 1; font-weight: 400; letter-spacing: 8px;
    white-space: nowrap;
  }
  .audience-band {
    position: absolute; left: 0; top: 292px; width: 100%; height: 95px;
    background: var(--mist); text-align: center; font-family: "Lato", sans-serif;
  }
  .audience {
    margin-top: 10px; color: var(--navy); font-weight: 700; font-size: 33px; line-height: 1.2;
  }
  .tagline {
    margin-top: 2px; color: var(--ink); font-style: italic; font-size: 19.5px;
    white-space: nowrap;
  }
  .portrait {
    position: absolute; left: 0; top: 387px; width: 735px; height: 282px;
    background: linear-gradient(90deg, var(--photo-dark) 0%, var(--photo-mid) 30%, var(--photo-light) 70%, var(--paper) 100%);
  }
  .promise {
    position: absolute; left: 290px; top: 438px; width: 550px;
    font-family: "La Belle Aurore", cursive; font-size: 40px; line-height: 48px;
    letter-spacing: 1px; color: var(--ink); text-align: right; white-space: nowrap;
  }
  .brand-mark {
    position: absolute; left: 545px; top: 588px;
    display: flex; align-items: center; gap: 8px;
    font-family: "Lato", sans-serif; font-weight: 700; font-size: 30px; color: var(--navy);
  }
  .brand-dot { width: 14px; height: 14px; border-radius: 50%; background: var(--accent); }
</style>
</head>
<body>
<main class="stage">
  <h1 class="stage-label">COVER PAGE REVISED</h1>
  <section class="cover">
    <header class="title-band">
      <div class="title-frame">
        <div class="title-main">THE PERSONAL</div>
        <div class="title-sub">BRAND COMPASS</div>
      </div>
    </header>
    <div class="audience-band">
      <p class="audience">For Pharmacy Entrepreneurs</p>
      <p class="tagline">The quick n’ dirty guide to creating a unique personal brand that attracts your ideal clients.</p>
    </div>
    <div class="portrait" role="img" aria-label="Black and white photo of the coach sitting on stone steps in a blazer"></div>
    <p class="promise">Step it up, get noticed, and<br>grow your client base.</p>
    <div class="brand-mark"><span class="brand-dot"></span>TorvelCast</div>
  </section>
</main>
</body>
</html>
```